Private Investigation Business Card Design

I need a business card for a new private investigation company named Brisk Inquiries. I perform mainly surveillance jobs, vehicle repossessions, document serves etc. The final design should aim for a professional look. The logo has a magnifying glass with stick man arms and legs and is in a running action to show the "Brisk" aspect of the name. If the colour scheme could remain the same as the website www.briskinquiries-demo.com.au with silvers,blacks and a couple electric blue highlights.
Industry/Entity Type
Business
Contact Information for Business Card
Morgan Kellaway
Brisk Inquiries
0487316204
PO Box 58, Carnwell NSW 2291
info@briskinquiries-demo.com.au
www.briskinquiries-demo.com.au
Look and feel

```html
<!DOCTYPE html>
<html lang="en">
<head>
<meta charset="utf-8">
<title>Brisk Inquiries – Business Card</title>
<link rel="stylesheet" href="https://fonts.googleapis.com/css2?family=Play:wght@400;700&family=Roboto:wght@400&display=swap">
<style>
  :root {
    --page-bg: #d9d7d4;
    --card-top: #ecebe8;
    --card-edge: #f7f6f4;
    --band-light: #c7c0be;
    --band-mid: #7d7675;
    --band-dark: #141414;
    --band-black: #060606;
    --ink: #2b2b2b;
    --logo-ink: #55575c;
    --name-gold: #c8a678;
    --glass-tone: #9c9792;
  }
  * { box-sizing: border-box; margin: 0; padding: 0; }
  html, body { width: 1200px; height: 969px; overflow: hidden; }
  body {
    background: var(--page-bg);
    position: relative;
    font-family: "Roboto", Arial, sans-serif;
  }
  .card {
    position: absolute;
    left: 100px;
    top: 200px;
    width: 1000px;
    height: 570px;
    background: var(--card-top);
    border: 2px solid var(--card-edge);
    border-radius: 6px;
    overflow: hidden;
    box-shadow: 0 10px 30px rgba(0,0,0,0.18);
  }
  .brand {
    position: absolute;
    left: 64px;
    top: 112px;
    display: flex;
    align-items: center;
    gap: 24px;
  }
  .brand-name {
    font-family: "Play", Arial, sans-serif;
    font-weight: 700;
    font-size: 66px;
    line-height: 1;
    color: var(--logo-ink);
    letter-spacing: 1px;
  }
  .brand-dot {
    width: 40px;
    height: 40px;
    border-radius: 50%;
    background: var(--logo-ink);
  }
  .info-band {
    position: absolute;
    left: 0;
    bottom: 0;
    width: 100%;
    height: 252px;
    background: linear-gradient(90deg, var(--band-light) 0%, var(--band-mid) 36%, var(--band-dark) 56%, var(--band-black) 100%);
  }
  .contact {
    position: absolute;
    left: 64px;
    top: 38px;
    color: var(--ink);
    font-size: 23px;
    line-height: 1.5;
  }
  .contact-line {
    display: flex;
    align-items: center;
    gap: 14px;
    height: 38px;
  }
  .contact-line svg { width: 22px; height: 22px; flex: none; }
  .address { margin-bottom: 4px; }
  .address p { height: 34px; line-height: 34px; }
  .glass-art {
    position: absolute;
    left: 487px;
    top: 0;
    width: 180px;
    height: 252px;
    background: radial-gradient(ellipse at 50% 35%, rgba(190,184,178,0.55) 0%, rgba(156,151,146,0.3) 45%, rgba(0,0,0,0) 75%);
  }
  .holder-name {
    position: absolute;
    left: 672px;
    top: 122px;
    font-family: "Play", Arial, sans-serif;
    font-weight: 400;
    font-size: 31px;
    color: var(--name-gold);
    letter-spacing: 0.5px;
  }
</style>
</head>
<body>
  <div class="card">
    <div class="brand">
      <span class="brand-name">Brisk Inquiries</span>
      <span class="brand-dot"></span>
    </div>

    <div class="info-band">
      <div class="contact">
        <div class="address">
          <p>PO Box 58</p>
          <p>Carnwell NSW 2291</p>
        </div>
        <div class="contact-line">
          <svg viewBox="0 0 24 24" aria-hidden="true"><path fill="#2b2b2b" d="M6.6 10.8a15.1 15.1 0 0 0 6.6 6.6l2.2-2.2a1 1 0 0 1 1-.25 11.4 11.4 0 0 0 3.6.57 1 1 0 0 1 1 1V20a1 1 0 0 1-1 1A17 17 0 0 1 3 4a1 1 0 0 1 1-1h3.5a1 1 0 0 1 1 1c0 1.25.2 2.45.57 3.57a1 1 0 0 1-.25 1z"/></svg>
          <span>0487 316 204</span>
        </div>
        <div class="contact-line">
          <svg viewBox="0 0 24 24" aria-hidden="true"><rect x="2" y="5" width="20" height="14" rx="1.5" fill="#2b2b2b"/><path d="M3 6.5l9 6.5 9-6.5" fill="none" stroke="#c7c0be" stroke-width="1.6"/></svg>
          <span>info@briskinquiries-demo.com.au</span>
        </div>
        <div class="contact-line">
          <svg viewBox="0 0 24 24" aria-hidden="true"><circle cx="12" cy="12" r="10" fill="#2b2b2b"/><path d="M2 12h20M12 2c3 3 3 17 0 20M12 2c-3 3-3 17 0 20" fill="none" stroke="#bdb6b4" stroke-width="1.3"/></svg>
          <span>www.briskinquiries-demo.com.au</span>
        </div>
      </div>

      <div class="glass-art" role="img" aria-label="Magnifying glass illustration"></div>

      <div class="holder-name">Morgan Kellaway</div>
    </div>
  </div>
</body>
</html>
```